RTavenor Business Cards & Letterhead

I have a logo but need a design for some new business cards. We are a Design-Build Firm that specializes in the design and construction of commercial projects.
the cards need to be professional. no cartoon stuff.
i would like to have the cards in AI format so I can update the card as needed. Logo is provided.
Our Address is: 4187 Marlowe Ct. Ashby, North Haven 27614

```html
<!DOCTYPE html>
<html lang="en">
<head>
<meta charset="utf-8">
<title>RTavenor Business Card</title>
<link href="https://fonts.googleapis.com/css2?family=Open+Sans:wght@400;700&display=swap" rel="stylesheet">
<style>
  :root {
    --backdrop: #4a4a4a;
    --card: #ffffff;
    --brand-blue: #0a5ea8;
    --ink: #333333;
    --wordmark-grey: #6b6b6b;
  }
  html, body {
    margin: 0;
    width: 1200px;
    height: 801px;
    overflow: hidden;
    background: var(--backdrop);
    font-family: "Open Sans", Arial, sans-serif;
  }
  .stage {
    position: relative;
    width: 1200px;
    height: 801px;
  }
  .card {
    position: absolute;
    top: 240px;
    width: 525px;
    height: 300px;
    background: var(--card);
    border-radius: 16px;
    border-bottom: 5px solid var(--brand-blue);
    box-shadow: 0 14px 30px rgba(0,0,0,0.35);
    overflow: hidden;
  }
  .card--front { left: 50px; }
  .card--back { left: 625px; }

  .brand {
    display: flex;
    align-items: center;
    gap: 8px;
  }
  .brand__square { background: var(--brand-blue); }
  .brand__name {
    font-weight: 700;
    color: var(--wordmark-grey);
    letter-spacing: 1px;
    text-transform: uppercase;
  }

  .card--front .brand {
    position: absolute;
    left: 32px;
    top: 30px;
  }
  .card--front .brand__square { width: 22px; height: 22px; }
  .card--front .brand__name { font-size: 30px; line-height: 1; }

  .side-tab {
    position: absolute;
    left: 0;
    top: 84px;
    width: 22px;
    height: 34px;
    background: var(--brand-blue);
  }
  .person {
    position: absolute;
    left: 40px;
    top: 80px;
  }
  .person__name {
    margin: 0;
    font-size: 20px;
    font-weight: 700;
    color: var(--brand-blue);
    text-transform: uppercase;
    letter-spacing: 0.5px;
  }
  .person__role {
    margin: 0;
    font-size: 14px;
    color: var(--ink);
  }

  .contact {
    position: absolute;
    left: 40px;
    top: 150px;
    margin: 0;
    padding: 0;
    list-style: none;
    font-size: 13.5px;
    color: var(--ink);
  }
  .contact li {
    display: flex;
    align-items: center;
    gap: 7px;
    line-height: 20px;
  }
  .contact svg { width: 12px; height: 12px; fill: var(--brand-blue); }

  .address {
    position: absolute;
    left: 58px;
    top: 225px;
    margin: 0;
    font-style: normal;
    font-size: 14px;
    line-height: 19px;
    color: var(--ink);
  }

  .card--back .brand {
    position: absolute;
    inset: 0;
    justify-content: center;
  }
  .card--back .brand__square { width: 34px; height: 34px; }
  .card--back .brand__name { font-size: 48px; line-height: 1; }
</style>
</head>
<body>
<main class="stage">

  <section class="card card--front" aria-label="Business card front">
    <div class="brand">
      <span class="brand__square"></span>
      <span class="brand__name">RTavenor</span>
    </div>

    <span class="side-tab"></span>
    <div class="person">
      <p class="person__name">Daniel Morrow</p>
      <p class="person__role">Managing Director</p>
    </div>

    <ul class="contact">
      <li>
        <svg viewBox="0 0 24 24" aria-hidden="true"><path d="M6.6 10.8a15 15 0 0 0 6.6 6.6l2.2-2.2a1 1 0 0 1 1-.25 11.4 11.4 0 0 0 3.6.57 1 1 0 0 1 1 1V20a1 1 0 0 1-1 1A17 17 0 0 1 3 4a1 1 0 0 1 1-1h3.5a1 1 0 0 1 1 1c0 1.25.2 2.45.57 3.57a1 1 0 0 1-.25 1z"/></svg>
        919 555 0142
      </li>
      <li>
        <svg viewBox="0 0 24 24" aria-hidden="true"><path d="M2 5h20v14H2z"/></svg>
        info@rtavenor.com
      </li>
      <li>
        <svg viewBox="0 0 24 24" aria-hidden="true"><circle cx="12" cy="12" r="10"/></svg>
        www.rtavenor.com
      </li>
    </ul>

    <address class="address">
      4187 Marlowe Ct. Ashby,<br>
      North Haven 27614
    </address>
  </section>

  <section class="card card--back" aria-label="Business card back">
    <div class="brand">
      <span class="brand__square"></span>
      <span class="brand__name">RTavenor</span>
    </div>
  </section>

</main>
</body>
</html>
```